Australian Trucking Company Requires Professional Looking Stationary

We require a professional looking stationary design that incorporates our newly designed logo.

Our business, called "Brell Haulage Contracting", provides contracting work, transport and logistics to business in Western Australia particularly with links to the mining sector.

We are a small business looking to expand and our new logo and our new stationary will help develop our brand image in our market place.

Target Market(s)

Businesses and Corporation with links to the Mining Sector

Industry/Entity Type

Small Business

Requirements
Must have
• The letterhead must have the following details:
The new logo

Text saying: "Brell Holdings Pty Ltd (ACN 582 316 907) ATF The Brell Discretionary Trust T/AS"
"ABN 71 834 209 553"
Address "P.O Box 817 Wattlegrove WA, 6958"
Phone: 08 9352 7140
Email: brellhaul@mailbox-example.com.au

The text on the letterhead should be editable as the details are likely to change in the near future. Provision should be made for a website address all though one isn't available at the moment.

The styling, layout and font text is entirely up to the designer.

```html
<!DOCTYPE html>
<html lang="en">
<head>
<meta charset="utf-8">
<title>Brell Haulage Contracting – Business Card</title>
<link href="https://fonts.googleapis.com/css2?family=Open+Sans:wght@400;600;700&display=swap" rel="stylesheet">
<style>
  :root {
    --brand-red: #e0222b;
    --brand-red-deep: #b5161e;
    --ink: #333333;
    --ink-soft: #666666;
    --charcoal: #1f1f1f;
    --silver: #b9b9b9;
    --paper: #ffffff;
    --backdrop: #ececec;
  }
  html, body {
    margin: 0;
    padding: 0;
    width: 1200px;
    height: 650px;
    overflow: hidden;
    background: var(--backdrop);
    font-family: "Open Sans", sans-serif;
  }
  .stage {
    position: relative;
    width: 1200px;
    height: 650px;
  }
  .card {
    position: absolute;
    top: 166px;
    width: 520px;
    height: 318px;
    border-radius: 22px;
    overflow: hidden;
    box-shadow: 0 6px 18px rgba(0,0,0,0.18);
  }
  .card--front { left: 50px; background: var(--paper); }
  .card--back {
    left: 630px;
    background: radial-gradient(circle at 50% 40%, #ec2a31 0%, var(--brand-red) 45%, var(--brand-red-deep) 100%);
  }
  .front-swoosh { position: absolute; inset: 0; }

  .brand {
    position: absolute;
    left: 34px;
    top: 30px;
    display: flex;
    align-items: center;
    gap: 16px;
  }
  .brand__mark {
    width: 62px;
    height: 62px;
    background: var(--ink-soft);
  }
  .brand__name {
    margin: 0;
    color: var(--brand-red);
    font-weight: 700;
    font-size: 27px;
    line-height: 28px;
    text-transform: uppercase;
    letter-spacing: 0.5px;
  }

  .holder {
    position: absolute;
    left: 330px;
    top: 160px;
    text-align: right;
    width: 140px;
  }
  .holder__name { color: var(--brand-red); font-weight: 700; font-size: 17px; line-height: 20px; }
  .holder__title { color: var(--ink-soft); font-size: 10px; }

  .contact {
    position: absolute;
    left: 40px;
    top: 168px;
    margin: 0;
    padding: 0;
    list-style: none;
    color: var(--ink);
    font-size: 12.5px;
  }
  .contact__item {
    display: flex;
    align-items: center;
    gap: 7px;
    height: 21px;
  }
  .contact__item:first-child { margin-bottom: 14px; }
  .contact__icon { width: 11px; height: 11px; fill: var(--ink); }

  .abn {
    position: absolute;
    right: 28px;
    bottom: 44px;
    color: var(--paper);
    font-size: 10.5px;
  }

  .back-name {
    position: absolute;
    left: 0; right: 0;
    top: 110px;
    text-align: center;
    color: var(--paper);
    font-weight: 700;
    font-size: 30px;
    line-height: 34px;
    text-transform: uppercase;
  }
  .back-web {
    position: absolute;
    left: 0; right: 0;
    bottom: 52px;
    text-align: center;
    color: var(--paper);
    font-size: 20px;
    letter-spacing: 0.5px;
  }
</style>
</head>
<body>
<div class="stage">

  <section class="card card--front">
    <svg class="front-swoosh" viewBox="0 0 520 318" width="520" height="318" aria-hidden="true">
      <defs>
        <linearGradient id="silverSweep" x1="0" x2="1" y1="0" y2="0">
          <stop offset="0" stop-color="#ffffff"/>
          <stop offset="0.5" stop-color="var(--silver)"/>
          <stop offset="1" stop-color="#8d8d8d"/>
        </linearGradient>
      </defs>
      <path d="M0,262 C150,285 340,250 520,196 L520,214 C340,262 150,296 0,282 Z" fill="url(#silverSweep)"/>
      <path d="M0,268 C90,272 190,286 270,284 C180,296 80,302 0,306 Z" fill="var(--charcoal)"/>
      <path d="M0,294 C160,300 340,262 520,218 L520,318 L0,318 Z" fill="var(--brand-red)"/>
    </svg>

    <div class="brand">
      <div class="brand__mark"></div>
      <h1 class="brand__name">Brell<br>Haulage<br>Contracting</h1>
    </div>

    <div class="holder">
      <div class="holder__name">Your Name</div>
      <div class="holder__title">Title</div>
    </div>

    <ul class="contact">
      <li class="contact__item">
        <svg class="contact__icon" viewBox="0 0 12 12"><path d="M6 1 L11.5 6 H10 V11 H7.5 V8 H4.5 V11 H2 V6 H0.5 Z"/></svg>
        P.O Box 817 Wattlegrove WA, 6958
      </li>
      <li class="contact__item">
        <svg class="contact__icon" viewBox="0 0 12 12"><path d="M2.5 1 L4.5 1 L5.3 3.8 L4 4.8 C4.6 6.2 5.8 7.4 7.2 8 L8.2 6.7 L11 7.5 L11 9.5 C11 10.4 10.3 11 9.4 11 C4.8 11 1 7.2 1 2.6 C1 1.7 1.6 1 2.5 1 Z"/></svg>
        08 9352 7140
      </li>
      <li class="contact__item">
        <svg class="contact__icon" viewBox="0 0 12 12"><path d="M0.5 2.5 H11.5 V9.5 H0.5 Z M1.2 3 L6 6.6 L10.8 3" stroke="#fff" stroke-width="0.9"/></svg>
        brellhaul@mailbox-example.com.au
      </li>
      <li class="contact__item">
        <svg class="contact__icon" viewBox="0 0 12 12"><circle cx="6" cy="6" r="5.2" fill="none" stroke="var(--ink)" stroke-width="1.1"/><path d="M0.8 6 H11.2 M6 0.8 C3.5 3.5 3.5 8.5 6 11.2 M6 0.8 C8.5 3.5 8.5 8.5 6 11.2" fill="none" stroke="var(--ink)" stroke-width="0.9"/></svg>
        www.brellhaulage-example.com
      </li>
    </ul>

    <div class="abn">ABN 71 834 209 553</div>
  </section>

  <section class="card card--back">
    <div class="back-name">Brell Haulage<br>Contracting</div>
    <div class="back-web">www.brellhaulage-example.com</div>
  </section>

</div>
</body>
</html>
```